New Website for World Wide Charity (KOLVAN)

We need a dynamic web design for our brand new charity organisation that will be working worldwide. We will be funded by donations so need to attract people to donate.

What We Do
We work to optimise the wellbeing of the planet, the animals and all that live within. Our slogan is Achieving Vibrational Equilibrium.

We have included a Powerpoint document which may help you understand what we need, it is just an idea for structure and style, it is not set in stone so feel free to be as creative as you like!
Updates

Designs look the same

Target Market(s)

Adults 18+ with an interest in animal, environmental. Businesses that may like to support our natural world or already support our natural world.

Number of Pages Required

3 page

Colors

Designer to choose colors to be used in the design.

Requirements
Must have
• We need the website to be easy to use and understand.

Web pages will be Home, What We Do, Who We Are, Success Stories, What You Can Do (Blog section), Seek Help, Donate, Join.
Nice to have
• Natural feel, easy to navigate, Ideally the website will look natural and organic.

Natural colours, blues, greens, sand, gold, brown, grey, silver, Orange and yellow for impact.
Should not have
• Should not have a dark coloured theme.

```html
<!DOCTYPE html>
<html lang="en">
<head>
<meta charset="utf-8">
<title>KOLVAN – Help Raise World Vibration</title>
<link href="https://fonts.googleapis.com/css2?family=Josefin+Sans:wght@600;700&family=Nunito+Sans:wght@400;600&display=swap" rel="stylesheet">
<style>
:root{
  --ink:#1e1e24;
  --text:#3c3c44;
  --brand:#3a3a86;
  --brand-dark:#2e2e70;
  --violet:#6b3d8f;
  --white:#ffffff;
  --footer:#121212;
  --footer-text:#e8e8e8;
  --rule:#2c2c2c;
}
*{box-sizing:border-box;margin:0;padding:0}
html,body{width:1200px;height:2596px;overflow:hidden}
body{font-family:"Nunito Sans",sans-serif;color:var(--text);background:var(--white);position:relative}
.heading{font-family:"Josefin Sans",sans-serif;font-weight:700;letter-spacing:2px;color:var(--ink)}
.btn{display:inline-block;background:var(--brand);color:var(--white);font-weight:600;font-size:16px;border-radius:3px;text-decoration:none}

.site-header{position:absolute;top:0;left:0;width:1200px;height:112px;display:flex;align-items:center}
.brand{position:absolute;left:78px;top:10px;width:96px;height:96px;border-radius:50%;border:3px solid #c9c2dc;background:#efe7f1;display:flex;align-items:center;justify-content:center;font-weight:600;font-size:15px;color:var(--brand);letter-spacing:1px}
.main-nav{position:absolute;left:256px;top:50px;display:flex;gap:34px;font-size:16px;color:var(--ink)}
.main-nav a{color:inherit;text-decoration:none}

.hero{position:absolute;top:112px;left:0;width:1200px;height:560px;background:linear-gradient(160deg,#8b8584 0%,#b98a5f 35%,#f1a447 55%,#d7782f 75%,#6a3f25 100%)}
.hero-copy{position:absolute;left:113px;top:126px;color:var(--white)}
.hero-title{font-size:52px;line-height:62px;color:var(--white);letter-spacing:3px}
.hero-sub{font-size:19px;margin-top:10px}
.hero .btn{margin-top:26px;padding:13px 15px}

.focus-cards{position:absolute;top:592px;left:113px;display:flex;gap:34px}
.card{width:301px;height:360px;background:var(--white);box-shadow:0 2px 8px rgba(0,0,0,.12);text-align:center;padding-top:30px}
.card svg{width:92px;height:92px}
.card h3{font-size:19px;margin-top:16px}
.card p{font-size:15px;line-height:24px;margin:20px 16px 0}
.card .btn{margin-top:24px;padding:9px 9px}

.feature{position:absolute}
.feature-img{position:absolute;width:360px;height:360px;border-radius:50%;border:5px solid #fff;box-shadow:0 0 0 3px #2f3a30,0 4px 14px rgba(0,0,0,.18)}
.feature-copy{position:absolute;width:445px}
.feature-copy h2{font-size:33px}
.feature-copy p{font-size:15.5px;line-height:26px;margin-top:22px}

.site-footer{position:absolute;top:2196px;left:0;width:1200px;height:400px;background:var(--footer);color:var(--footer-text)}
.footer-brand{position:absolute;left:113px;top:40px;width:138px;height:138px;border-radius:50%;border:4px solid #d8d0e8;background:#efe7f1;display:flex;align-items:center;justify-content:center;color:var(--brand);font-weight:600;font-size:18px;letter-spacing:1px}
.footer-about{position:absolute;left:112px;top:190px;width:250px;font-size:15.5px;line-height:24px}
.footer-col{position:absolute;top:50px}
.footer-col h4{font-family:"Josefin Sans",sans-serif;font-weight:700;font-size:16px;letter-spacing:2px;color:var(--white);margin-bottom:20px}
.footer-col li{list-style:none;font-size:15.5px;line-height:30px;padding-left:2px}
.social{display:flex;gap:13px}
.social span{width:14px;height:14px;border-radius:50%;background:var(--white);display:block}
.footer-rule{position:absolute;left:110px;top:290px;width:980px;height:1px;background:var(--rule)}
.footer-base{position:absolute;top:336px;left:112px;width:975px;display:flex;justify-content:space-between;font-size:15.5px}
</style>
</head>
<body>

<header class="site-header">
  <div class="brand">KOLVAN</div>
  <nav class="main-nav">
    <a href="#">HOME</a><a href="#">WHAT WE DO</a><a href="#">WHO WE ARE</a><a href="#">SUCCESS STORIES</a><a href="#">WHAT YOU CAN DO</a><a href="#">DONATE AND JOIN</a>
  </nav>
</header>

<section class="hero" role="img" aria-label="Woman meditating on a rock at sunset with birds flying over hills">
  <div class="hero-copy">
    <h1 class="heading hero-title">HELP RAISE WORLD<br>VIBRATION</h1>
    <p class="hero-sub">Achieving Vibrational Equilibrium</p>
    <a class="btn" href="#">MAKE A DIFFERENCE</a>
  </div>
</section>

<section class="focus-cards">
  <article class="card">
    <svg viewBox="0 0 92 92" fill="none" stroke="#6b3d8f" stroke-width="3" stroke-linecap="round">
      <circle cx="46" cy="50" r="30"/><path d="M46 20v-10M46 12c-6-6-12-2-12-2s4 6 12 2M46 12c6-6 12-2 12-2s-4 6-12 2"/>
      <path d="M20 62c8 10 18 12 26 10M72 62c-8 10-18 12-26 10"/>
    </svg>
    <h3 class="heading">ENVIRONMENT</h3>
    <p>Sed ut perspiciatis unde omnis iste natus error sit voluptatem accusantium doloremque laudantium, totam rem aperiam</p>
    <a class="btn" href="#">FIND OUT MORE</a>
  </article>
  <article class="card">
    <svg viewBox="0 0 92 92" fill="none" stroke="#553f92" stroke-width="4">
      <ellipse cx="14" cy="44" rx="7" ry="9"/><ellipse cx="33" cy="22" rx="8" ry="12"/><ellipse cx="59" cy="22" rx="8" ry="12"/><ellipse cx="78" cy="44" rx="7" ry="9"/>
      <path d="M46 46c-14 0-26 20-22 30 4 8 14 2 22 2s18 6 22-2c4-10-8-30-22-30z"/>
    </svg>
    <h3 class="heading">ANIMAL</h3>
    <p>Sed ut perspiciatis unde omnis iste natus error sit voluptatem accusantium doloremque laudantium, totam rem aperiam</p>
    <a class="btn" href="#">FIND OUT MORE</a>
  </article>
  <article class="card">
    <svg viewBox="0 0 92 92" fill="none" stroke="#4a3a8a" stroke-width="4" stroke-linejoin="round">
      <circle cx="46" cy="14" r="8"/>
      <path d="M12 30h68v8H56v14l8 36h-8l-10-26-10 26h-8l8-36V38H12z"/>
    </svg>
    <h3 class="heading">HUMAN</h3>
    <p>Sed ut perspiciatis unde omnis iste natus error sit voluptatem accusantium doloremque laudantium, totam rem aperiam</p>
    <a class="btn" href="#">FIND OUT MORE</a>
  </article>
</section>

<section class="feature">
  <div class="feature-img" style="left:175px;top:1045px;background:linear-gradient(180deg,#8b9bb0 0%,#d9e2ea 30%,#4f7a3e 60%,#2c4a24 100%)" role="img" aria-label="Misty tea plantation hills"></div>
  <div class="feature-copy" style="left:637px;top:1122px"><h2 class="heading">ENVIRONMENT</h2>
  <p>Sed ut perspiciatis unde omnis iste natus error sit voluptatem accusantium doloremque laudantium, totam rem aperiam, eaque ipsa quae ab illo inventore veritatis et quasi architecto beatae vitae dicta sunt explicabo. Nemo enim ipsam voluptatem quia voluptas sit aspernatur aut odit aut fugit, sed quia consequuntur magni dolores eos qui ratione voluptatem sequi nesciunt.</p></div>

  <div class="feature-copy" style="left:118px;top:1474px"><h2 class="heading">ANIMAL</h2>
  <p>Sed ut perspiciatis unde omnis iste natus error sit voluptatem accusantium doloremque laudantium, totam rem aperiam, eaque ipsa quae ab illo inventore veritatis et quasi architecto beatae vitae dicta sunt explicabo. Nemo enim ipsam voluptatem quia voluptas sit aspernatur aut odit aut fugit, sed quia consequuntur magni dolores eos qui ratione voluptatem sequi nesciunt.</p></div>
  <div class="feature-img" style="left:665px;top:1398px;background:linear-gradient(160deg,#5d8a3c 0%,#d8d8d2 45%,#6b5a48 75%,#3a4a2a 100%)" role="img" aria-label="Young panda resting in a tree"></div>

  <div class="feature-img" style="left:175px;top:1752px;background:linear-gradient(180deg,#4f6b4a 0%,#c9a070 35%,#d9c93a 60%,#3e5a32 100%)" role="img" aria-label="Smiling hiker with a backpack on a trail"></div>
  <div class="feature-copy" style="left:637px;top:1826px"><h2 class="heading">HUMAN</h2>
  <p>Sed ut perspiciatis unde omnis iste natus error sit voluptatem accusantium doloremque laudantium, totam rem aperiam, eaque ipsa quae ab illo inventore veritatis et quasi architecto beatae vitae dicta sunt explicabo. Nemo enim ipsam voluptatem quia voluptas sit aspernatur aut odit aut fugit, sed quia consequuntur magni dolores eos qui ratione voluptatem sequi nesciunt.</p></div>
</section>

<footer class="site-footer">
  <div class="footer-brand">KOLVAN</div>
  <p class="footer-about">Sed ut perspiciatis unde omnis iste natus error sit voluptatem accusantium doloremque</p>
  <div class="footer-col" style="left:405px"><h4>GET INVOLVED</h4><ul><li>Join Us</li><li>Fundraise</li><li>Donate</li><li>Shop</li></ul></div>
  <div class="footer-col" style="left:616px"><h4>GET HELP</h4><ul><li>Contact Us</li><li>Media</li></ul></div>
  <div class="footer-col" style="left:770px"><h4>LEGAL</h4><ul><li>Terms and Conditions</li><li>Cookies</li><li>Privacy Policy</li></ul></div>
  <div class="footer-col" style="left:982px"><h4>FOLLOW US</h4><div class="social"><span></span><span></span><span></span><span></span></div></div>
  <div class="footer-rule"></div>
  <div class="footer-base"><span>Charity: 4419072358</span><span>©Copyrights 2021 Company Name &nbsp;| &nbsp; All Rights Reserved</span></div>
</footer>

</body>
</html>
```